Merrowin Vodka logo and label design

We would like a logo and bottle label design for a new line of Ultra-Premium Vodka. The Company is called Merrowin Spirits and is based in Brisbane, Australia. We would like a 'Gatsby/Prohibition era vibe to the design. We want to keep it minimalistic and sleek. We strongly prefer a minimalist design and colour palette. Black,Gold,Grey,White,Silver,Red and Blue

The bottle will be similar in shape to Castellane/Blue Heron. There will also need to be space on the label for required information, as well as short bio of the company, which will be provided to the winning design.
Updates

We would like to add the polish code of arms for Opoczno. Have attached link for reference. https://www.crestarchive-demo.net/crestwiki/index.php?title=Opoczno

Target Market(s)

Luxury brand customers

Logo Text

Merrowin Ultra-Premium Vodka

Logo styles of interest
Wordmark Logo
Lettermark Logo
Requirements
Must have
• This is the first release from our new Vodka label. We want a logo and bottle label that reflects a premium product. We very much like Prohibition/Gatsby era themed bottles and labels. The label and bottle should be elegant and clean.
Should not have
• Anything too busy or confusing.

```html
<!DOCTYPE html>
<html lang="en">
<head>
<meta charset="utf-8">
<title>Merrowin Ultra-Premium Vodka – Label Designs</title>
<link rel="stylesheet" href="https://fonts.googleapis.com/css2?family=Cinzel:wght@400&family=Josefin+Sans:wght@600&display=swap">
<style>
  :root {
    --canvas: #ffffff;
    --label-black: #111111;
    --label-charcoal: #2c2c2c;
    --gold-light: #f6e08a;
    --gold: #d4a537;
    --gold-deep: #a8781f;
  }
  * { margin: 0; padding: 0; box-sizing: border-box; }
  html, body {
    width: 1200px; height: 1190px; overflow: hidden;
    background: var(--canvas);
  }
  .canvas { position: relative; width: 1200px; height: 1190px; }
  .label {
    position: absolute; width: 210px; height: 375px;
  }
  .label--lined { left: 233px; top: 528px; }
  .label--plain { left: 752px; top: 521px; }
  .label__shape { position: absolute; inset: 0; }
  .label__content {
    position: absolute; inset: 0;
    display: flex; flex-direction: column; align-items: center;
    color: var(--gold);
  }
  .label__mark {
    position: absolute; left: 50%; width: 40px; height: 40px;
    margin-left: -20px; border-radius: 50%;
    background: linear-gradient(135deg, var(--gold-light), var(--gold) 50%, var(--gold-deep));
  }
  .label__wordmark {
    position: absolute; left: 0; right: 0; text-align: center;
    font-family: "Cinzel", serif; font-weight: 400;
    font-size: 26px; letter-spacing: 0.5px; line-height: 1;
    color: var(--gold);
  }
  .label__tagline {
    position: absolute; left: 0; right: 0; text-align: center;
    font-family: "Josefin Sans", sans-serif; font-weight: 600;
    font-size: 6.5px; letter-spacing: 2.6px; line-height: 1;
    color: var(--gold);
  }
  .spec-table {
    position: absolute; left: 48px; width: 113px; height: 43px;
    border: 1px solid var(--gold);
    display: grid; grid-template-columns: 1fr 1fr; grid-template-rows: 1fr 1fr;
    font-family: "Cinzel", serif; font-size: 5.5px; color: var(--gold);
  }
  .spec-table__cell { display: flex; align-items: center; padding-left: 7px; }
  .spec-table__cell--right { padding-left: 6px; border-left: 1px solid var(--gold); margin: 3px 0; }
  .spec-table__cell--top { border-bottom: 1px solid var(--gold); margin-left: 6px; padding-left: 1px; }
  .spec-table__cell--top.spec-table__cell--right { margin-left: 0; margin-right: 6px; margin-bottom: 0; padding-left: 6px; }
</style>
</head>
<body>
<main class="canvas">
  <svg width="0" height="0" style="position:absolute" aria-hidden="true">
    <defs>
      <linearGradient id="gold-rim" x1="0" y1="0" x2="1" y2="1">
        <stop offset="0" stop-color="#f6e08a"/>
        <stop offset="0.45" stop-color="#d4a537"/>
        <stop offset="0.7" stop-color="#a8781f"/>
        <stop offset="1" stop-color="#f0d27a"/>
      </linearGradient>
      <linearGradient id="black-body" x1="0" y1="0" x2="1" y2="0">
        <stop offset="0" stop-color="#0e0e0e"/>
        <stop offset="0.55" stop-color="#2e2e2e"/>
        <stop offset="1" stop-color="#0e0e0e"/>
      </linearGradient>
      <linearGradient id="gold-line" x1="0" y1="0" x2="1" y2="0">
        <stop offset="0" stop-color="#a8781f" stop-opacity="0.2"/>
        <stop offset="0.5" stop-color="#e9c45a"/>
        <stop offset="1" stop-color="#a8781f" stop-opacity="0.2"/>
      </linearGradient>
    </defs>
  </svg>

  <!-- Variant A: arched label with gold rules -->
  <section class="label label--lined" aria-label="Merrowin label, ruled variant">
    <svg class="label__shape" viewBox="0 0 210 375" aria-hidden="true">
      <path d="M0 42 H42 C52 16 76 0 105 0 C134 0 158 16 168 42 H210 V330 H168 C158 358 134 374 105 374 C76 374 52 358 42 330 H0 Z" fill="url(#gold-rim)"/>
      <path d="M6 48 H46 C56 22 78 5 105 5 C132 5 154 22 164 48 H204 V324 H164 C154 352 132 369 105 369 C78 369 56 352 46 324 H6 Z" fill="url(#black-body)"/>
      <rect x="75" y="18" width="60" height="1.6" fill="url(#gold-line)"/>
      <rect x="68" y="30" width="74" height="1.6" fill="url(#gold-line)"/>
      <rect x="58" y="42" width="94" height="1.6" fill="url(#gold-line)"/>
      <rect x="46" y="307" width="118" height="1.6" fill="url(#gold-line)"/>
      <rect x="60" y="322" width="90" height="1.6" fill="url(#gold-line)"/>
      <rect x="72" y="338" width="66" height="1.6" fill="url(#gold-line)"/>
    </svg>
    <div class="label__content">
      <span class="label__mark" style="top:105px"></span>
      <h1 class="label__wordmark" style="top:187px">MERROWIN</h1>
      <p class="label__tagline" style="top:212px">ULTRA-PREMIUM VODKA</p>
      <div class="spec-table" style="top:243px">
        <span class="spec-table__cell spec-table__cell--top">BATCH</span>
        <span class="spec-table__cell spec-table__cell--right spec-table__cell--top">ALC/VOL</span>
        <span class="spec-table__cell">YEAR</span>
        <span class="spec-table__cell spec-table__cell--right">ML</span>
      </div>
    </div>
  </section>

  <!-- Variant B: plain arched label -->
  <section class="label label--plain" aria-label="Merrowin label, plain variant">
    <svg class="label__shape" viewBox="0 0 210 375" aria-hidden="true">
      <path d="M0 42 H42 C52 16 76 0 105 0 C134 0 158 16 168 42 H210 V330 H168 C158 358 134 374 105 374 C76 374 52 358 42 330 H0 Z" fill="url(#gold-rim)"/>
      <path d="M6 48 H46 C56 22 78 5 105 5 C132 5 154 22 164 48 H204 V324 H164 C154 352 132 369 105 369 C78 369 56 352 46 324 H6 Z" fill="url(#black-body)"/>
    </svg>
    <div class="label__content">
      <span class="label__mark" style="top:98px"></span>
      <h2 class="label__wordmark" style="top:180px">MERROWIN</h2>
      <p class="label__tagline" style="top:205px">ULTRA-PREMIUM VODKA</p>
      <div class="spec-table" style="top:236px">
        <span class="spec-table__cell spec-table__cell--top">BATCH</span>
        <span class="spec-table__cell spec-table__cell--right spec-table__cell--top">ALC/VOL</span>
        <span class="spec-table__cell">YEAR</span>
        <span class="spec-table__cell spec-table__cell--right">ML</span>
      </div>
    </div>
  </section>
</main>
</body>
</html>
```